Brand Identity Stationary Package

Hello I'm looking for a full branding package for my Property Management Company. I have a logo but looking to have the following
Business Card
Email signature
Facebook cover photo
Letterhead (word.doc)
#10 Envelope
Pocket Folder - link to 9x12 pocket folder design specs https://www.printorbit-example.ca/marketing-materials/presentation-folders
would like everything to match and be brand identifiable. The company looks after residential properties/apartments and some commercial properties. Attached is a zip of the files.
For Business Card
Name: Gareth Lindqvist
Position: Operations Manager
Number: 1 (555) 384-2917
Email: Gareth@harborkey-example.ca
Website: Harborkey-example.ca
Property Management

```html
<!DOCTYPE html>
<html lang="en">
<head>
<meta charset="utf-8">
<title>Harborkey Business Card</title>
<link rel="stylesheet" href="https://fonts.googleapis.com/css2?family=Inter:ital,wght@0,400;0,600;0,700;1,400&display=swap">
<style>
  :root {
    --backdrop: #e9e4dd;
    --card-top: #f7f6f3;
    --card-top-shade: #e6e3de;
    --ink: #1c1c1c;
    --band: #1e1e1e;
    --green-light: #5f9433;
    --green-dark: #2f5716;
    --name-ink: #f3ead9;
    --detail-ink: #e9e2d2;
    --divider: #e9dcc6;
  }
  * { margin: 0; padding: 0; box-sizing: border-box; }
  html, body {
    width: 1200px;
    height: 969px;
    overflow: hidden;
    background: var(--backdrop);
    font-family: "Inter", sans-serif;
  }
  .canvas {
    position: relative;
    width: 1200px;
    height: 969px;
  }
  .business-card {
    position: absolute;
    left: 166px;
    top: 236px;
    width: 868px;
    height: 494px;
    border-radius: 26px;
    overflow: hidden;
    background: linear-gradient(180deg, var(--card-top) 0%, var(--card-top-shade) 100%);
    box-shadow: 0 18px 40px rgba(0, 0, 0, 0.18);
  }
  .brand-name {
    position: absolute;
    left: 0;
    right: 0;
    top: 92px;
    text-align: center;
    font-family: "Inter", sans-serif;
    font-weight: 700;
    font-size: 74px;
    letter-spacing: 6px;
    line-height: 1;
    color: var(--ink);
  }
  .divider-band {
    position: absolute;
    left: 0;
    top: 282px;
    width: 100%;
    height: 15px;
    background: var(--band);
  }
  .contact-panel {
    position: absolute;
    left: 0;
    top: 297px;
    width: 100%;
    height: 197px;
    background: linear-gradient(135deg, var(--green-light) 0%, #4a7a26 45%, var(--green-dark) 100%);
  }
  .person {
    position: absolute;
    right: 454px;
    top: 68px;
    text-align: right;
  }
  .person-name {
    font-weight: 600;
    font-size: 37px;
    line-height: 1.1;
    color: var(--name-ink);
  }
  .person-role {
    font-style: italic;
    font-weight: 400;
    font-size: 21px;
    color: var(--name-ink);
    margin-top: 2px;
  }
  .vertical-rule {
    position: absolute;
    left: 440px;
    top: 62px;
    width: 2px;
    height: 76px;
    background: var(--divider);
  }
  .contact-list {
    position: absolute;
    left: 468px;
    top: 62px;
    list-style: none;
  }
  .contact-item {
    display: flex;
    align-items: center;
    gap: 12px;
    height: 27px;
    font-size: 21px;
    color: var(--detail-ink);
  }
  .contact-icon {
    width: 17px;
    height: 17px;
    flex: none;
    fill: var(--detail-ink);
  }
</style>
</head>
<body>
<main class="canvas">
  <article class="business-card">
    <h1 class="brand-name">HARBORKEY</h1>
    <div class="divider-band"></div>
    <section class="contact-panel">
      <div class="person">
        <p class="person-name">Gareth Lindqvist</p>
        <p class="person-role">Operations Manager</p>
      </div>
      <div class="vertical-rule"></div>
      <ul class="contact-list">
        <li class="contact-item">
          <svg class="contact-icon" viewBox="0 0 24 24" aria-hidden="true"><path d="M6.6 10.8a15.1 15.1 0 0 0 6.6 6.6l2.2-2.2a1 1 0 0 1 1-.25 11.4 11.4 0 0 0 3.6.57 1 1 0 0 1 1 1V20a1 1 0 0 1-1 1A17 17 0 0 1 3 4a1 1 0 0 1 1-1h3.5a1 1 0 0 1 1 1c0 1.25.2 2.45.57 3.57a1 1 0 0 1-.25 1z"/></svg>
          <span>1 (555) 384-2917</span>
        </li>
        <li class="contact-item">
          <svg class="contact-icon" viewBox="0 0 24 24" aria-hidden="true"><path d="M3 5h18a1 1 0 0 1 1 1v12a1 1 0 0 1-1 1H3a1 1 0 0 1-1-1V6a1 1 0 0 1 1-1zm1 2.2V17h16V7.2l-8 5.3z"/></svg>
          <span>Gareth@harborkey-example.ca</span>
        </li>
        <li class="contact-item">
          <svg class="contact-icon" viewBox="0 0 24 24" aria-hidden="true"><path d="M12 2a10 10 0 1 0 0 20 10 10 0 0 0 0-20zm-1 17.9A8 8 0 0 1 4.2 10.5L9 15.3v1a2 2 0 0 0 2 2zm6.9-2.5A2 2 0 0 0 16 16h-1v-3a1 1 0 0 0-1-1H8v-2h2a1 1 0 0 0 1-1V7h2a2 2 0 0 0 2-2v-.4a8 8 0 0 1 2.9 12.8z"/></svg>
          <span>www.Harborkey-example.ca</span>
        </li>
      </ul>
    </section>
  </article>
</main>
</body>
</html>
```